Maplecrest Disability - Social Security Disability Attorneys

Our company is expanding to attract clients nationwide for our social security disability practice. We have a logo, but I am looking for a creative and elegant letterhead that projects an image of being technologically advanced but still professional enough for the legal field. I am looking for the "wow factor" combined with this is still professional enough for a law practice.

Requesting letterhead and business card design
Updates

Had to update and change the logo. The previous logo had a typo. Please send updates with the new logo for consideration. The letterhead and business cards should be professional enough to be used for a law firm. Thanks.

Industry/Entity Type

Law Practice, Law Firm, Healthcare Industry, Government

Colors

Designer to choose colors to be used in the design.

Requirements
Nice to have
• **Please create a vertical design for the business card**

```html
<!DOCTYPE html>
<html lang="en">
<head>
<meta charset="utf-8">
<title>Maplecrest Disability – Stationery</title>
<link href="https://fonts.googleapis.com/css2?family=Lato:wght@400;700&family=Montserrat:wght@400;500;700&display=swap" rel="stylesheet">
<style>
  :root{
    --bg:#bebec0;
    --paper:#ffffff;
    --brand-blue:#4169d6;
    --logo-blue:#3f5fc4;
    --card-blue:#5673bf;
    --orange:#f0812b;
    --ink:#222222;
    --sig-fill:#eef0f5;
  }
  *{margin:0;padding:0;box-sizing:border-box}
  html,body{width:1200px;height:848px;overflow:hidden;background:var(--bg)}
  .canvas{position:relative;width:1200px;height:848px;background:var(--bg)}

  /* Letterhead */
  .letterhead{position:absolute;left:151px;top:118px;width:455px;height:623px;background:var(--paper);
    font-family:'Lato',sans-serif;color:var(--ink);overflow:hidden}
  .brand{position:absolute;text-align:center;color:var(--logo-blue);font-family:'Lato',sans-serif;font-weight:400}
  .brand .mark{display:block;width:9px;height:9px;border-radius:50%;background:var(--orange);margin:0 auto 6px}
  .brand .name{display:block;text-transform:uppercase;letter-spacing:.08em;white-space:nowrap}
  .brand .tagline{display:block;text-transform:uppercase;letter-spacing:.18em;white-space:nowrap}
  .letterhead .brand{left:18px;top:34px;width:144px}
  .letterhead .brand .name{font-size:11.4px}
  .letterhead .brand .tagline{font-size:3.6px;margin-top:2px}

  .lh-contact{position:absolute;left:321px;top:36px;border-left:1px solid var(--orange);padding-left:6px;
    font-size:7px;line-height:10.4px}
  .lh-contact .row{display:flex;align-items:center;gap:5px}
  .lh-contact svg{width:7px;height:7px;flex:none}

  .letter-body{position:absolute;left:25px;top:147px;width:405px;font-size:8.6px;line-height:10.3px}
  .letter-body p{margin-bottom:10px}
  .letter-body .date{margin-bottom:11px}
  .letter-body .salutation{font-weight:700;font-size:11px;margin:3px 0 11px}
  .letter-body .copy{text-align:justify;margin-bottom:9.6px}
  .letter-body .closing{margin-top:21px}
  .signature{width:116px;height:22px;background:var(--sig-fill);margin-top:12px}

  .band{position:absolute;left:0;bottom:0;display:block}

  /* Business cards */
  .card{position:absolute;top:234px;width:213px;height:373px;overflow:hidden;font-family:'Montserrat',sans-serif}
  .card-front{left:627px;background:var(--paper);color:var(--ink);text-align:center}
  .card-back{left:864px;background:var(--card-blue);color:#fff;text-align:center}
  .card .brand{left:0;width:213px}
  .card-front .brand{top:40px}
  .card-back .brand{top:60px;color:#fff}
  .card-back .brand .mark{background:#fff}
  .card .brand .name{font-size:13px}
  .card .brand .tagline{font-size:4px;margin-top:2px}

  .holder{position:absolute;top:132px;left:0;width:213px}
  .holder .person{font-weight:700;font-size:12.5px;color:var(--orange);letter-spacing:.01em}
  .holder .role{display:flex;align-items:center;justify-content:center;gap:3px;font-size:9.5px;margin-top:1px}
  .holder .role::before,.holder .role::after{content:"";width:28px;height:1px;background:var(--orange)}

  .card-address{position:absolute;top:192px;left:0;width:213px;font-size:8.8px;line-height:12.4px;font-weight:500}
  .card-icons{position:absolute;top:233px;left:0;width:213px;display:flex;justify-content:center;gap:16px}
  .card-icons svg{width:9px;height:9px}
  .card-lines{position:absolute;top:260px;left:0;width:213px;font-size:8.8px;line-height:14px;font-weight:500}

  .card-sectors{position:absolute;top:317px;left:0;width:213px;font-size:8.8px;line-height:12.4px;font-weight:500}
</style>
</head>
<body>
<main class="canvas">

  <!-- Letterhead -->
  <section class="letterhead">
    <div class="brand">
      <span class="mark"></span>
      <span class="name">Maplecrest Disability</span>
      <span class="tagline">Social Security Disability Attorneys</span>
    </div>

    <address class="lh-contact" style="font-style:normal">
      <div>Suite 4,level 12,Alder</div>
      <div>Street Fairview NSW 2100</div>
      <div class="row" style="margin-top:2px">
        <svg viewBox="0 0 10 10"><path d="M2 1l2 2-1 1.2c.6 1.2 1.6 2.2 2.8 2.8L7 6l2 2-1.4 1.4C4.5 9 1 5.5.6 2.4z" fill="var(--orange)"/></svg>
        <span>555-214-7390</span>
      </div>
      <div class="row">
        <svg viewBox="0 0 10 10"><rect x="0.5" y="2" width="9" height="6" fill="var(--orange)"/><path d="M.5 2L5 5.5 9.5 2" stroke="#fff" stroke-width=".8" fill="none"/></svg>
        <span>Info@maplecrestdisability.com</span>
      </div>
      <div class="row">
        <svg viewBox="0 0 10 10"><circle cx="5" cy="5" r="4.5" fill="var(--orange)"/><path d="M5 .5v9M.5 5h9M2 2.5c2 1 4 1 6 0M2 7.5c2-1 4-1 6 0" stroke="#fff" stroke-width=".6" fill="none"/></svg>
        <span>www.maplecrestdisability.com</span>
      </div>
    </address>

    <div class="letter-body">
      <p class="date">January-03-2020</p>
      <p>Mr, Peter Lang<br>President</p>
      <p>Brightline Corporation<br>48 Alder Road, Suite# 10<br>Fairview, State, 120023</p>
      <p class="salutation">Dear Mr, Peter</p>
      <p class="copy">Lorem ipsum dolor sit amet, consectetur adipisicing elit, sed do eiusmod tempor incididunt ut labore et dolore magna aliqua. Ut enim ad minim veniam, quis nostrud exercitation ullamco laboris nisi ut aliquip ex ea commodo consequat. Duis aute irure dolor in reprehenderit in voluptate velit esse cillum dolore eu fugiat nulla pariatur.</p>
      <p class="copy">Lorem ipsum dolor sit amet, consectetur adipisicing elit, sed do eiusmod tempor incididunt ut labore et dolore magna aliqua. Ut enim ad minim veniam, quis nostrud exercitation ullamco laboris nisi ut aliquip ex ea commodo consequat. Duis aute irure dolor in reprehenderit in voluptate velit esse cillum dolore eu fugiat nulla pariatur.</p>
      <p class="copy">Lorem ipsum dolor sit amet, consectetur adipisicing elit, sed do eiusmod tempor incididunt ut labore et dolore magna aliqua. Ut enim ad minim veniam, quis nostrud exercitation ullamco laboris nisi ut aliquip ex ea commodo consequat.</p>
      <p class="copy">Excepteur sint occaecat cupidatat non proident, sunt in culpa qui officia deserunt mollit anim id est laborum. re et dolore magnam aliquam quaerat voluptatem.</p>
      <p class="closing">Regards</p>
      <div class="signature" role="img" aria-label="Handwritten signature of Daniel Whitford"></div>
    </div>

    <svg class="band" width="455" height="30" viewBox="0 0 455 30">
      <rect x="0" y="2" width="81" height="7" fill="var(--brand-blue)"/>
      <rect x="85" y="2" width="82" height="7" fill="var(--orange)"/>
      <polygon points="171,2 294,2 287,9 171,9" fill="var(--brand-blue)"/>
      <polygon points="0,15 290,15 304,1 455,1 455,30 0,30" fill="var(--brand-blue)"/>
    </svg>
  </section>

  <!-- Business card front -->
  <section class="card card-front">
    <div class="brand">
      <span class="mark"></span>
      <span class="name">Maplecrest Disability</span>
      <span class="tagline">Social Security Disability Attorneys</span>
    </div>
    <div class="holder">
      <div class="person">OWEN CALDWELL</div>
      <div class="role">Co-Founder</div>
    </div>
    <div class="card-address">Suite 4,level 12,Alder<br>Street Fairview NSW 2100</div>
    <div class="card-icons">
      <svg viewBox="0 0 10 10"><path d="M2 1l2 2-1 1.2c.6 1.2 1.6 2.2 2.8 2.8L7 6l2 2-1.4 1.4C4.5 9 1 5.5.6 2.4z" fill="var(--orange)"/></svg>
      <svg viewBox="0 0 10 10"><rect x="0.5" y="2" width="9" height="6" fill="var(--orange)"/><path d="M.5 2L5 5.5 9.5 2" stroke="#fff" stroke-width=".8" fill="none"/></svg>
      <svg viewBox="0 0 10 10"><circle cx="5" cy="5" r="4.5" fill="var(--orange)"/><path d="M5 .5v9M.5 5h9M2 2.5c2 1 4 1 6 0M2 7.5c2-1 4-1 6 0" stroke="#fff" stroke-width=".6" fill="none"/></svg>
    </div>
    <div class="card-lines">555-214-7390<br>Info@maplecrestdisability.com<br>www.maplecrestdisability.com</div>
    <svg class="band" width="213" height="16" viewBox="0 0 213 16">
      <rect x="0" y="0" width="38" height="3.5" fill="var(--brand-blue)"/>
      <rect x="40" y="0" width="38" height="3.5" fill="var(--orange)"/>
      <polygon points="80,0 137,0 133.5,3.5 80,3.5" fill="var(--brand-blue)"/>
      <polygon points="0,6 134,6 140,0 213,0 213,16 0,16" fill="var(--card-blue)"/>
    </svg>
  </section>

  <!-- Business card back -->
  <section class="card card-back">
    <div class="brand">
      <span class="mark"></span>
      <span class="name">Maplecrest Disability</span>
      <span class="tagline">Social Security Disability Attorneys</span>
    </div>
    <div class="card-sectors">Law Practice, Law Firm,<br>Healthcare Industry, Government</div>
  </section>

</main>
</body>
</html>
```